Updated Business Card Re-design (Logo Provided)

I am needing to update our business cards for our practice, Brightfield Care Partners. We are a personal injury and wellness practice. The final design should be elegant and classy, but a type of card people would want to keep. Any samples should only have Dr. Tomas Verlinde on the template.
Updates

Went on vacation/holiday

Need extra days to review

Target Market(s)

Personal Injury clients, wellness clients

Industry/Entity Type

Personal Injury, medical, wellness

Contact Information for Business Card

dr and practice name, offerings

Requirements
Must have
• Single sided, this will be printed on a transparent business card, no exceptions.

```html
<!DOCTYPE html>
<html lang="en">
<head>
<meta charset="UTF-8">
<title>Brightfield Care Partners – Business Card</title>
<link rel="stylesheet" href="https://fonts.googleapis.com/css2?family=Poppins:wght@400;500;600&display=swap">
<style>
  :root {
    --page-bg: #e4ded6;
    --card-clear: #f3f4f5;
    --card-frost: #e6e9ec;
    --navy: #0a1740;
    --navy-deep: #050d2c;
    --ink: #0c1a48;
    --brand-blue: #1f6db3;
    --orange: #e08a1e;
    --green: #2f8a45;
    --light-text: #e9ebf2;
  }
  * { margin: 0; padding: 0; box-sizing: border-box; }
  html, body {
    width: 1200px; height: 1008px; overflow: hidden;
    background: var(--page-bg);
    font-family: "Poppins", sans-serif;
  }
  .card {
    position: absolute; left: 80px; top: 206px;
    width: 1040px; height: 596px;
    border-radius: 36px; overflow: hidden;
    background: linear-gradient(160deg, var(--card-clear) 0%, var(--card-frost) 100%);
    border: 1.5px solid #ffffff;
    box-shadow: 0 18px 40px rgba(40, 30, 20, 0.18);
  }
  .card-waves { position: absolute; inset: 0; width: 100%; height: 100%; }
  .name-marker {
    position: absolute; left: 0; top: 92px; width: 15px; height: 34px;
    background: var(--orange);
  }
  .doctor-name {
    position: absolute; left: 37px; top: 86px;
    font-size: 33px; font-weight: 600; color: var(--ink); letter-spacing: 0.3px;
  }
  .contact-list { position: absolute; left: 38px; top: 163px; list-style: none; }
  .contact-list li {
    display: flex; align-items: center; height: 41px;
    font-size: 27px; font-weight: 400; color: var(--ink);
  }
  .contact-list svg { width: 24px; height: 24px; margin-right: 9px; fill: var(--ink); }
  .practice-name {
    position: absolute; right: 38px; top: 72px;
    display: flex; align-items: center; gap: 12px;
    font-size: 27px; font-weight: 600; color: var(--brand-blue);
  }
  .practice-dot { width: 20px; height: 20px; border-radius: 50%; background: var(--orange); }
  .services { position: absolute; right: 22px; top: 280px; text-align: right; }
  .services-title {
    font-size: 24px; font-weight: 600; color: var(--brand-blue);
    letter-spacing: 1.5px; margin-right: 16px; margin-bottom: 6px;
  }
  .services-list { list-style: none; }
  .services-list li {
    font-size: 22px; font-weight: 400; color: var(--light-text);
    height: 32.6px; line-height: 32.6px; letter-spacing: 0.4px;
  }
  .services-list li::after {
    content: ""; display: inline-block; width: 7px; height: 7px; border-radius: 50%;
    background: var(--orange); margin-left: 10px; vertical-align: middle;
  }
  .address {
    position: absolute; left: 38px; top: 518px;
    font-size: 22px; color: var(--light-text); letter-spacing: 0.3px;
  }
</style>
</head>
<body>
  <div class="card">
    <svg class="card-waves" viewBox="0 0 1040 596" preserveAspectRatio="none" aria-hidden="true">
      <defs>
        <linearGradient id="navyFill" x1="0" y1="0" x2="0" y2="1">
          <stop offset="0" stop-color="#0e1d52"/>
          <stop offset="1" stop-color="#040b26"/>
        </linearGradient>
      </defs>
      <path d="M0 370 C 120 420, 260 410, 420 360 C 480 340, 540 320, 578 310 C 520 340, 430 390, 340 410 C 220 436, 100 430, 0 398 Z" fill="var(--green)"/>
      <path d="M482 352 C 620 300, 760 255, 880 235 C 950 224, 1000 228, 1040 242 L1040 262 C 990 246, 940 244, 880 252 C 770 268, 640 310, 482 352 Z" fill="var(--orange)"/>
      <path d="M0 422 C 150 470, 300 460, 470 390 C 620 330, 790 268, 900 256 C 960 250, 1005 254, 1040 266 L1040 596 L0 596 Z" fill="url(#navyFill)"/>
    </svg>

    <div class="name-marker"></div>
    <h1 class="doctor-name">Dr. Tomas Verlinde, D.C.</h1>

    <ul class="contact-list">
      <li><svg viewBox="0 0 24 24"><path d="M3 9c0-3 4-5 9-5s9 2 9 5v2h-5V9H8v2H3zM6 12h12l2 8H4z"/></svg>555.014.2380</li>
      <li><svg viewBox="0 0 24 24"><path d="M7 1h10a2 2 0 0 1 2 2v18a2 2 0 0 1-2 2H7a2 2 0 0 1-2-2V3a2 2 0 0 1 2-2zm0 3v14h10V4zm5 15.5a1.2 1.2 0 1 0 0 2.4 1.2 1.2 0 0 0 0-2.4z"/></svg>555.014.7761</li>
      <li><svg viewBox="0 0 24 24"><path d="M2 6h20v12H2zm2 1.5 8 6 8-6z"/></svg>info@brightfieldcare.com</li>
      <li><svg viewBox="0 0 24 24"><path d="M12 2a10 10 0 1 0 0 20 10 10 0 0 0 0-20zm-2 4 3 2-1 3-3 1-2-3zm5 6 3 1-1 4-3 2-1-4z"/></svg>brightfieldcare.com</li>
    </ul>

    <div class="practice-name"><span class="practice-dot"></span>Brightfield Care Partners</div>

    <div class="services">
      <h2 class="services-title">OUR SERVICES</h2>
      <ul class="services-list">
        <li>Auto Accident Care</li>
        <li>Primary Care</li>
        <li>Medical Weight loss</li>
        <li>Physical Therapy</li>
        <li>Pain Management</li>
        <li>ortho services</li>
        <li>Chiropractice</li>
      </ul>
    </div>

    <p class="address">4820 Meadowline Road, Suite 12, Fairhaven, GA 30999</p>
  </div>
</body>
</html>
```